Judicial election website to attract voters

I need a simple one-page web design for a judicial election. I'm going to put up one picture, maybe two. The picture I have needs a little touch-up (whiten teeth for example). I have 3 paragraphs of text. I'd like a "Donate" button that can link to a CoinDrift account. I'd also like a little background design, like the Constitution or something like that. There's a couple other little things but that's the bulk of it.

Target Market(s)

Involved voters and some media

Industry/Entity Type

Legal

Number of Pages Required

1 page

Font styles to use
Sans Serif

Requirements
Must have
• My picture, text, donate button
• Phrase "Remember to vote August 30, 2016!"
Nice to have
• Perhaps a second photo, maybe a short 30 second video of me talking directly to the voters, cool background: Constitution, something judgey.
Should not have
• Not sure ... profanity, I guess.

```html
<!DOCTYPE html>
<html lang="en">
<head>
<meta charset="utf-8">
<title>Marianne – Judicial Election</title>
<link href="https://fonts.googleapis.com/css2?family=Montserrat:wght@500&family=Roboto:wght@400&family=Open+Sans:wght@400&display=swap" rel="stylesheet">
<style>
  :root {
    --orange: #e2650a;
    --ink: #1a1a1a;
    --dark: #15110e;
    --text: #4a4a4a;
    --white: #ffffff;
    --dot: #d4d4d4;
  }
  * { margin: 0; padding: 0; box-sizing: border-box; }
  html, body { width: 874px; height: 1200px; overflow: hidden; background: var(--white); }
  body { position: relative; font-family: "Open Sans", sans-serif; }
  h2 { font-weight: 400; }

  .hero {
    position: absolute; left: 0; top: 0; width: 874px; height: 374px;
    background: linear-gradient(160deg, #5b4a3c 0%, #3a2a20 35%, #7a5d3e 60%, #a28a6c 80%, #4a3a2c 100%);
  }
  .hero-strip { position: absolute; left: 0; top: 374px; width: 874px; height: 8px; background: #141110; }
  .brand-bar {
    position: absolute; left: 81px; top: 25px; width: 712px; height: 63px;
    background: rgba(255,255,255,0.92);
    display: flex; align-items: center; justify-content: center;
  }
  .brand-name {
    font-family: "Montserrat", sans-serif; font-weight: 500; font-size: 29px;
    color: var(--orange); letter-spacing: 0.5px;
  }
  .slide-caption {
    position: absolute; left: 81px; top: 245px; width: 436px; height: 65px;
    background: rgba(30,28,27,0.88);
    color: var(--white); font-family: "Roboto", sans-serif; font-size: 22px;
    display: flex; align-items: center; padding-left: 20px;
  }
  .slide-nav { position: absolute; left: 457px; top: 310px; display: flex; gap: 2px; }
  .slide-nav span {
    width: 29px; height: 24px; background: var(--orange);
    display: flex; align-items: center; justify-content: center;
  }

  .about { position: absolute; left: 0; top: 382px; width: 874px; height: 250px; }
  .portrait {
    position: absolute; left: 82px; top: 50px; width: 148px; height: 148px;
    border-radius: 50%; border: 2px solid #e6e6e6; padding: 3px; background: var(--white);
  }
  .portrait div {
    width: 100%; height: 100%; border-radius: 50%;
    background: radial-gradient(circle at 50% 45%, #d9a88e 0%, #c9b79a 40%, #cfd3d8 75%);
  }
  .tagline {
    position: absolute; left: 260px; top: 42px;
    font-family: "Roboto", sans-serif; font-size: 19px; color: var(--ink);
    display: flex; align-items: center; gap: 8px;
  }
  .tagline .sep { width: 7px; height: 7px; border-radius: 50%; background: var(--dot); }
  .about-body { position: absolute; left: 261px; top: 75px; width: 535px; }
  .bio { font-size: 8.8px; line-height: 22.4px; color: var(--text); }
  .more-link {
    margin-top: 5px;
    font-family: "Roboto", sans-serif; font-size: 11.5px; color: var(--orange);
    display: flex; align-items: center; gap: 5px;
  }

  .video-section {
    position: absolute; left: 0; top: 632px; width: 874px; height: 420px;
    background: linear-gradient(180deg, #1d130c 0%, #3a2615 45%, #2b1d12 75%, #1a120c 100%);
  }
  .video-title {
    position: absolute; left: 0; width: 874px; top: 54px; text-align: center;
    font-family: "Roboto", sans-serif; font-size: 21px; color: var(--white);
  }
  .video-frame {
    position: absolute; left: 190px; top: 128px; width: 493px; height: 240px;
    border: 4px solid var(--white);
    background: linear-gradient(135deg, #a9b2b5 0%, #d8dcdc 40%, #f2f2f0 60%, #5c6064 100%);
  }
  .play { position: absolute; left: 215px; top: 85px; }

  .donate-band {
    position: absolute; left: 0; top: 1052px; width: 874px; height: 77px; background: var(--orange);
  }
  .donate-button {
    position: absolute; left: 350px; top: 17px; width: 175px; height: 44px;
    background: var(--dark); border-radius: 3px; color: var(--white);
    font-family: "Roboto", sans-serif; font-size: 15px; letter-spacing: 0.5px;
    display: flex; align-items: center; justify-content: center;
  }

  .footer {
    position: absolute; left: 0; top: 1129px; width: 874px; height: 71px; background: var(--dark);
    color: var(--white); font-size: 9px;
  }
  .footer-links { position: absolute; left: 82px; top: 16px; }
  .footer-links span { margin: 0 5px; }
  .copyright { position: absolute; left: 81px; top: 37px; }
  .social { position: absolute; left: 714px; top: 25px; display: flex; gap: 4px; }
  .social span { width: 16px; height: 16px; border-radius: 50%; background: #2c5fa8; border: 1px solid var(--white); }
  .social span.red { background: #c0281e; }
</style>
</head>
<body>
  <header class="hero" role="img" aria-label="Photo of a judge's gavel and scales of justice on law books"></header>
  <div class="hero-strip"></div>
  <div class="brand-bar"><span class="brand-name">MARIANNE</span></div>
  <div class="slide-caption">REMEMBER TO VOTE AUGUST 30, 2016!</div>
  <div class="slide-nav">
    <span><svg width="8" height="10" viewBox="0 0 8 10"><path d="M6 1 L2 5 L6 9" fill="none" stroke="#fff" stroke-width="2"/></svg></span>
    <span><svg width="8" height="10" viewBox="0 0 8 10"><path d="M2 1 L6 5 L2 9" fill="none" stroke="#fff" stroke-width="2"/></svg></span>
  </div>

  <section class="about">
    <div class="portrait"><div role="img" aria-label="Portrait photo of the candidate"></div></div>
    <h2 class="tagline">EXPERIENCED <span class="sep"></span> DEDICATED <span class="sep"></span> RESPECTED</h2>
    <div class="about-body">
      <div class="bio">
        <p>Marianne was born and raised in Tampa Florida, the daughter of an air-conditioning repairman who later opened his own successful business. As the first in her family to go to college, her parents could not have been more proud as she finished her degree at the Gulf Coast University, then continued on to Bayshore State School of Law where she graduated with honors.</p>
        <p>Dedicating her life to public service in central Florida, she has spent the last 18 years as a prosecutor fighting for victims of child abuse and sexual abuse in Orange and Osceola counties.</p>
      </div>
      <div class="more-link">
        <svg width="11" height="11" viewBox="0 0 11 11"><circle cx="5.5" cy="5.5" r="5.5" fill="#e2650a"/><path d="M4.3 3 L6.8 5.5 L4.3 8" fill="none" stroke="#fff" stroke-width="1.6"/></svg>
        MORE DETAILS
      </div>
    </div>
  </section>

  <section class="video-section" role="img" aria-label="Dim library shelves of old law books">
    <h2 class="video-title">WATCH OUR VIDEO
      <svg width="40" height="42" viewBox="0 0 40 42" style="vertical-align:-22px;margin-left:-4px"><path d="M2 6 C18 0 36 6 30 24 L36 24 L24 38 L20 20 L26 22 C30 10 18 4 2 6 Z" fill="#fff"/></svg>
    </h2>
    <div class="video-frame" role="img" aria-label="Video still of a hand signing a document with a pen">
      <svg class="play" width="62" height="62" viewBox="0 0 62 62"><circle cx="31" cy="31" r="31" fill="rgba(20,20,20,0.85)"/><path d="M24 18 L46 31 L24 44 Z" fill="#fff"/></svg>
    </div>
  </section>

  <section class="donate-band">
    <div class="donate-button">DONATE NOW</div>
  </section>

  <footer class="footer">
    <div class="footer-links">Privacy Policy<span>|</span>Contact Us</div>
    <div class="copyright">© 2016 Marianne. All Rights Reserved.</div>
    <div class="social"><span></span><span></span><span></span><span class="red"></span></div>
  </footer>
</body>
</html>
```